Business Card Design

We need a business card designed for our new company. Prefer a black card with white logo & writing.

Contact Information for Business Card

Ted Galloway, address: 7-4812 Fernhollow Road, Abbotsford, BC, V3K 8R2, Office Phone: 604-712-3390, Cell: 604-947-2164, Email: ted@resinworkshub.ca

Colors

Designer to choose only greyscale colors for use in the design.

```html
<!DOCTYPE html>
<html lang="en">
<head>
<meta charset="utf-8">
<title>Resin Works Hub — Business Card</title>
<link href="https://fonts.googleapis.com/css2?family=Montserrat:wght@400;500;700;800&display=swap" rel="stylesheet">
<style>
  :root {
    --backdrop: #1e1e1e;
    --card: #000000;
    --ink: #ffffff;
    --peak-light: #e6e6e6;
    --peak-dark: #000000;
  }
  * { margin: 0; padding: 0; box-sizing: border-box; }
  html, body { width: 1200px; height: 900px; overflow: hidden; }
  body {
    background: var(--backdrop);
    font-family: "Montserrat", Arial, sans-serif;
    color: var(--ink);
    position: relative;
  }
  .card {
    position: absolute;
    left: 341px;
    width: 518px;
    height: 296px;
    background: var(--card);
    overflow: hidden;
  }
  .card--front { top: 141px; }
  .card--back { top: 463px; }

  .holder-name {
    position: absolute;
    left: 31px;
    top: 60px;
    font-size: 24px;
    letter-spacing: 1.5px;
    font-weight: 400;
    text-transform: uppercase;
  }
  .holder-name strong { font-weight: 800; }

  .contact-list { list-style: none; position: absolute; left: 32px; top: 124px; }
  .contact-item { display: flex; align-items: center; height: 36px; margin-bottom: 18px; }
  .contact-icon { width: 25px; height: 28px; flex: none; margin-right: 9px; }
  .contact-text { font-size: 13.5px; line-height: 18px; font-weight: 400; letter-spacing: 0.2px; }

  .brand-mark {
    position: absolute;
    right: 30px;
    top: 40px;
    width: 120px;
    text-align: center;
    font-weight: 800;
    font-size: 18px;
    line-height: 21px;
    text-transform: uppercase;
    letter-spacing: 0.5px;
  }

  .peak-illustration {
    position: absolute;
    left: 241px;
    top: 168px;
    width: 277px;
    height: 128px;
    background: linear-gradient(160deg, var(--peak-dark) 30%, var(--peak-light) 100%);
    opacity: 0.55;
  }

  .brand-lockup {
    position: absolute;
    inset: 0;
    display: flex;
    align-items: center;
    justify-content: center;
    font-weight: 800;
    font-size: 40px;
    letter-spacing: 1px;
    text-transform: uppercase;
  }
</style>
</head>
<body>
  <section class="card card--front">
    <h1 class="holder-name"><strong>Ted</strong> Galloway</h1>

    <ul class="contact-list">
      <li class="contact-item">
        <svg class="contact-icon" viewBox="0 0 25 28" aria-hidden="true">
          <polygon points="12.5,0 25,7 25,21 12.5,28 0,21 0,7" fill="#fff"/>
          <path d="M12.5 6.5a5 5 0 0 0-5 5c0 3.8 5 9.5 5 9.5s5-5.7 5-9.5a5 5 0 0 0-5-5z" fill="#000"/>
          <circle cx="12.5" cy="11.5" r="2" fill="#fff"/>
        </svg>
        <p class="contact-text">7-4812 Fernhollow Road<br>Abbotsford, BC, V3K 8R2</p>
      </li>
      <li class="contact-item">
        <svg class="contact-icon" viewBox="0 0 25 28" aria-hidden="true">
          <polygon points="12.5,0 25,7 25,21 12.5,28 0,21 0,7" fill="#fff"/>
          <path d="M9 7.5l2.2 3.2-1.4 1.6c.9 2 2.3 3.5 4.2 4.4l1.6-1.4 3.2 2.2-1.2 2.4c-5.6-.4-9.6-4.6-10-10z" fill="#000"/>
        </svg>
        <p class="contact-text">604-712-3390<br>604-947-2164&nbsp; Cell</p>
      </li>
      <li class="contact-item">
        <svg class="contact-icon" viewBox="0 0 25 28" aria-hidden="true">
          <polygon points="12.5,0 25,7 25,21 12.5,28 0,21 0,7" fill="#fff"/>
          <rect x="6" y="9" width="13" height="10" rx="1.5" fill="#000"/>
          <path d="M6.5 10l6 4.5 6-4.5" fill="none" stroke="#fff" stroke-width="1.4"/>
        </svg>
        <p class="contact-text">ted@resinworkshub.ca<br>www.resinworkshub.ca</p>
      </li>
    </ul>

    <div class="brand-mark">Resin Works<br>Hub</div>

    <div class="peak-illustration" role="img" aria-label="White mountain peak illustration rising from the bottom right corner"></div>
  </section>

  <section class="card card--back">
    <div class="brand-lockup">Resin Works Hub</div>
  </section>
</body>
</html>
```